Website and Logo Design for new niche job board.

Hello, We are an up and coming job board that is focused on LEGITIMATE companies that hire telecommuters to work from home. We are looking to build a highly interactive job board and forum/blog. The site is called TaskHarbor.com We focus on helping work at home moms, older workers and college students in work at home positions. We offer free job posting and advertising to the employer and free resume posting to the job seeker. (Free everything basically) Our revenue will be based from banner ads on the site so we will need a space on both sides of the page for those ads. 

The software we are using to build the job board part of the site can be viewed at www.plinkforge.example. It is already built! We do not need job software but a dashboard look to our main page - PLEASE pay attention to this! Do not submit a job board look as we have the job board page built!

These are the sites I like - please use these links to understand exactly the look I want

 

http://www.brightmuffins.example/

http://www.evagrant.example/

http://www.ladiesatwork.example/

https://www.findingnannies.example/index.asp?
Updates

Hi everyone- I think there might be some confusion to what we are looking for. We have the job board software through www.plinkforge.example, we are looking for the main page to be built around that. Basically we want a dashboard look with lots of little boxes to add content such as different articles,podcasts, forums,blogs,highlight different companies hiring,etc. If you can add scrolling or moving objects would be ideal. The less of a static website the better. You dont have to worry about the jobboard portion just the main page when you click on www.TaskHarbor.com, we really need it to capture peoples attention and see its a staffing firm AND a job board, forum, etc for work at home positions.  Here are some looks I am aiming for -

http://www.evagrant.example/

Please use alot of color- lime green, oranges, turquiose blue, purple, lots and lots of color please! I like more tropical colors. Thanks! I dont like red and dark colors at all. Thanks

Target Market(s)

Target customers will be both companies and individuals. The individuals will be a broad age range that are interested in working from home. The companies will be small to large corporations that have valid work from home positions.

Requirements
Must have
• I want a colorful site with moving objects and scrolling text - static sites are bland, and outdated- I am looking for a HIGHLY interactive board. Please do not just throw a template up there and expect me to like it. I am picky and want an ultra sleek design and eye catching. I can make an out of the box website myself, I have 3 other companies and did that -  PLEASE PLEASE DO NOT SHOW ME A COOKIE!
Nice to have
• Would be very nice to have the HTML sliced up for finished designs.
Should not have
• just not boring and static. Anything new and creative is where we are heading.

```html
<!DOCTYPE html>
<html lang="en">
<head>
<meta charset="utf-8">
<title>TaskHarbor.com – Work From Home Jobs</title>
<link href="https://fonts.googleapis.com/css2?family=Roboto+Condensed:wght@400;700&family=Open+Sans:wght@400;600;700&family=Ubuntu:wght@500&display=swap" rel="stylesheet">
<style>
:root{
  --turquoise:#13b5c2;
  --turquoise-deep:#0d8f9a;
  --purple:#7a3fb5;
  --purple-deep:#5c2b8c;
  --orange:#ff8a1f;
  --orange-deep:#e0661a;
  --lime:#6cb52a;
  --lime-deep:#4f8f17;
  --ink:#1d1d1d;
  --blue:#0d5e8c;
  --white:#fff;
  --rule:#d6d6d6;
  --row:#f4f8f8;
}
*{margin:0;padding:0;box-sizing:border-box}
html,body{width:1200px;height:1177px;overflow:hidden;background:var(--white)}
body{font-family:"Open Sans",sans-serif;color:var(--ink);position:relative}
.abs{position:absolute}
.cond{font-family:"Roboto Condensed",sans-serif;font-weight:700}

.topbar{left:0;top:0;width:1200px;height:42px;background:var(--turquoise)}
.toplinks{right:83px;top:13px;color:var(--white);font-size:11.5px;font-weight:700;letter-spacing:.3px}
.toplinks span{margin:0 6px}

.brand{left:131px;top:95px;font-size:28px;font-weight:700;color:var(--ink);display:flex;align-items:center;gap:8px}
.brand-mark{width:16px;height:16px;background:var(--orange)}
.promo-top{left:469px;top:42px;width:594px;height:104px;background:linear-gradient(90deg,#1d5f8a,#3f6fb0 35%,#d9452e 65%,#f1e3b0)}

.nav{left:0;top:146px;width:1200px;height:36px;background:var(--purple)}
.nav a{position:absolute;top:0;height:36px;line-height:36px;color:var(--white);font-size:14px;text-decoration:none;font-family:"Roboto Condensed",sans-serif;font-weight:700;letter-spacing:.3px}
.nav .active{background:var(--orange);height:27px;line-height:27px;top:4px;padding:0 24px;border-radius:3px}
.shade{left:0;top:182px;width:1200px;height:33px;background:linear-gradient(#e4e4ec,#fff 60%,#f0f0f4)}

.band{left:0;top:215px;width:1200px;height:313px;background:radial-gradient(ellipse at 45% 30%,#2cc6cf,var(--turquoise-deep) 75%)}
.band-title{color:var(--white);font-size:18px;letter-spacing:.4px}

.panel{background:var(--white);border-radius:12px;box-shadow:4px 4px 0 rgba(0,0,0,.18),0 2px 6px rgba(0,0,0,.25)}
.label{font-size:11.5px;font-weight:700;letter-spacing:.3px}
.field{width:240px;height:27px;border:1px solid #777;font-size:10.5px;color:#888;padding:6px 6px;letter-spacing:.3px}
.btn{background:var(--lime);color:var(--white);font-size:11.5px;text-align:center;line-height:21px;width:69px;height:21px;font-weight:600}
.adv{color:var(--purple);font-size:11px;font-weight:700;letter-spacing:.6px;display:flex;align-items:center;gap:8px}
.quote{font-size:17px;text-align:center;line-height:21px;width:130px}

.emp-title{color:var(--blue);font-size:12.5px;letter-spacing:.3px}
.small{font-size:10.5px;line-height:12.5px;letter-spacing:.2px}
.more{font-size:10px;font-weight:700}
.badge{width:83px;height:79px;border:4px solid var(--orange);border-radius:8px;background:#fff;box-shadow:0 3px 0 #aaa}
.other{color:var(--orange-deep);font-size:12px;font-weight:600;letter-spacing:.3px}
.emp-name{font-size:24px;font-weight:700;color:#333}

.section{font-size:18px;letter-spacing:.3px}
.tab{height:23px;line-height:23px;color:var(--white);font-size:11px;text-align:center;background:var(--purple);font-weight:600}
.tab.on{background:var(--orange)}
.morejobs{color:var(--blue);font-size:10px;font-weight:700;letter-spacing:.8px}
.jobs{left:153px;top:634px;width:529px}
.job{position:relative;height:57px;border-bottom:1px solid var(--rule);font-size:10.5px;letter-spacing:.4px;background:var(--row)}
.job:nth-child(even){background:#fbfbfb}
.job > div{position:absolute;top:23px}
.job .title{top:14px;line-height:12px}
.job .title b{display:block;font-weight:700}

.card{border-radius:6px;color:var(--white);box-shadow:0 2px 3px rgba(0,0,0,.3);overflow:hidden}
.card.blog{background:var(--purple)}
.card.article{background:var(--turquoise-deep)}
.card.podcast{background:var(--lime-deep)}
.card h3{font-family:"Ubuntu",sans-serif;font-weight:500;font-size:23px;position:absolute;left:19px}
.card p{position:absolute;left:19px;font-size:10.5px;font-weight:700;line-height:12.5px;letter-spacing:.3px}
.card .rm{font-size:9.5px}

.footer{left:0;top:1143px;width:1200px;height:34px;background:var(--turquoise);color:var(--white);font-size:11px;font-weight:700;text-align:center;line-height:34px;letter-spacing:.6px}
</style>
</head>
<body>

<div class="abs topbar"></div>
<div class="abs toplinks">Login<span>|</span>Register<span>|</span>Contact Us</div>

<div class="abs brand"><span class="brand-mark"></span>TaskHarbor.com</div>
<div class="abs promo-top" role="img" aria-label="Banner ad with dice: Why Gamble? We're a Sure Thing!"></div>

<nav class="abs nav">
  <a class="active" style="left:160px">HOME</a>
  <a style="left:307px">MY ACCOUNT</a>
  <a style="left:483px">FIND JOBS</a>
  <a style="left:633px">POST RESUME</a>
  <a style="left:803px">REGISTER</a>
  <a style="left:945px">EMPLOYER</a>
</nav>
<div class="abs shade"></div>

<section class="abs band"></section>
<h2 class="abs band-title cond" style="left:138px;top:225px">JOB SEARCH</h2>
<h2 class="abs band-title cond" style="left:731px;top:225px">FEATURED EMPLOYER</h2>

<div class="abs panel" style="left:138px;top:264px;width:467px;height:246px"></div>
<div class="abs label" style="left:157px;top:283px">Job Title:</div>
<div class="abs field" style="left:157px;top:302px">(e.g., nurse)</div>
<div class="abs label" style="left:157px;top:340px">Skills/Keywords:</div>
<div class="abs field" style="left:157px;top:358px">(e.g., healthcare, sales)</div>
<div class="abs label" style="left:157px;top:397px">Location:</div>
<div class="abs field" style="left:157px;top:415px">(city, state, or zip code)</div>
<div class="abs btn" style="left:239px;top:463px">Search</div>
<div class="abs quote cond" style="left:439px;top:342px">“FIND THE JOB YOU DESERVE MOST”</div>
<div class="abs adv" style="left:448px;top:465px">Advance Search
  <svg width="16" height="16" viewBox="0 0 16 16"><circle cx="8" cy="8" r="8" fill="#5c2b8c"/><path d="M4.5 6.5h7L8 11z" fill="#fff"/></svg>
</div>

<div class="abs panel" style="left:731px;top:261px;width:323px;height:245px"></div>
<div class="abs badge" style="left:758px;top:280px"></div>
<div class="abs emp-title" style="left:864px;top:287px">Meadowline Insurance</div>
<div class="abs small" style="left:864px;top:312px;width:180px">Lorem Ipsum is simply dummy text of the printing and typesetting industry. Lorem Ipsum has been the industry's standard dummy text ever since the 1500s.</div>
<div class="abs more" style="left:974px;top:388px">Read More</div>
<div class="abs other" style="left:750px;top:428px">Other Employers</div>
<div class="abs emp-name" style="left:752px;top:458px">Vantro</div>
<div class="abs emp-name" style="left:850px;top:458px">Orbex</div>
<div class="abs emp-name" style="left:960px;top:458px">Balden</div>

<h2 class="abs section cond" style="left:134px;top:560px">LATEST JOBS</h2>
<div class="abs panel" style="left:138px;top:597px;width:560px;height:410px"></div>
<div class="abs tab on" style="left:153px;top:611px;width:125px">By Area of Interest</div>
<div class="abs tab" style="left:286px;top:611px;width:125px">By Field</div>
<div class="abs tab" style="left:419px;top:611px;width:125px">By Qualification</div>
<div class="abs morejobs" style="left:619px;top:618px">MORE JOBS</div>

<div class="abs jobs">
  <div class="job"><div style="left:11px">April 05</div><div class="title" style="left:99px"><b>Data Entry</b>Lorem Ipsum is simply<br>dummy text of the printing</div><div style="left:281px">Tresla</div><div style="left:359px;font-weight:700">Computer</div><div style="left:449px">$10/Hour</div></div>
  <div class="job"><div style="left:11px">April 05</div><div class="title" style="left:99px"><b>Lorum Ipsum</b>Lorem Ipsum is simply<br>dummy text of the printing</div><div style="left:281px">Tresla</div><div style="left:359px;font-weight:700">Demo</div><div style="left:447px">$10/Hour</div></div>
  <div class="job"><div style="left:11px">April 05</div><div class="title" style="left:99px"><b>Lorum Ipsum</b>Lorem Ipsum is simply<br>dummy text of the printing</div><div style="left:281px">Tresla</div><div style="left:359px;font-weight:700">Demo</div><div style="left:447px">$10/Hour</div></div>
  <div class="job"><div style="left:11px">April 05</div><div class="title" style="left:99px"><b>Lorum Ipsum</b>Lorem Ipsum is simply<br>dummy text of the printing</div><div style="left:281px">Tresla</div><div style="left:359px;font-weight:700">Demo</div><div style="left:447px">$10/Hour</div></div>
  <div class="job"><div style="left:11px">April 05</div><div class="title" style="left:99px"><b>Lorum Ipsum</b>Lorem Ipsum is simply<br>dummy text of the printing</div><div style="left:281px">Tresla</div><div style="left:359px;font-weight:700">Demo</div><div style="left:447px">$10/Hour</div></div>
  <div class="job"><div style="left:11px">April 05</div><div class="title" style="left:99px"><b>Lorum Ipsum</b>Lorem Ipsum is simply<br>dummy text of the printing</div><div style="left:281px">Tresla</div><div style="left:359px;font-weight:700">Demo</div><div style="left:447px">$10/Hour</div></div>
</div>

<div class="abs card blog" style="left:733px;top:596px;width:327px;height:121px">
  <h3 style="top:10px">Our blog</h3>
  <p style="top:45px;width:180px">Lorem Ipsum is simply dummy text of the printing and typesetting industry.</p>
  <p class="rm" style="top:86px">Read More</p>
  <div class="abs" style="left:214px;top:6px;width:106px;height:107px;background:var(--orange);border-radius:12px"></div>
</div>

<div class="abs card article" style="left:733px;top:738px;width:327px;height:122px">
  <h3 style="top:10px">Latest Article</h3>
  <p style="top:42px;width:195px">John. K.<br>Lorem Ipsum is simply dummy text of the printing and typesetting industry.</p>
  <p class="rm" style="top:98px">Read More</p>
  <div class="abs" role="img" aria-label="Author portrait photo" style="left:220px;top:8px;width:100px;height:108px;border:2px solid #fff;border-radius:8px;background:linear-gradient(160deg,#c9b59a,#6d5a4a 60%,#3b3b44)"></div>
</div>

<div class="abs card podcast" style="left:733px;top:881px;width:327px;height:121px">
  <h3 style="top:32px;left:23px;line-height:29px">Listen Live<br>Our Podcasts</h3>
  <div class="abs" role="img" aria-label="Headphones with podcast feed icon" style="left:205px;top:8px;width:112px;height:108px;border-radius:50%;background:radial-gradient(circle,#f7901e 35%,#444 36%,#2a2a2a 70%,transparent 71%)"></div>
</div>

<div class="abs" role="img" aria-label="Ad banner: New Home... New Life Style, beach scene, Keystone Townhome" style="left:137px;top:1024px;width:559px;height:105px;background:linear-gradient(180deg,#2a6f9a,#5fb0c6 45%,#e6d9ae 75%,#f2ead2)"></div>
<div class="abs" role="img" aria-label="Ad banner: We Stand Out from the Rest" style="left:733px;top:1024px;width:328px;height:105px;background:linear-gradient(180deg,#ff5a7a,#e0305a 55%,#7a2a4a 95%)"></div>

<footer class="abs footer">©2010 taskharbor.com - All Rights Reserved</footer>

</body>
</html>
```